Business Card Design for Varomir Facility Services

We are looking for a Business Card Design for the Company "Varomir Facility Services."
Front side:
- Company Logo (small)
- Company Name, address, pohone, website and personal data.
- white background, for text e.g. company colors (blue or green like in the logo)
Please use following data:
Company data:
Varomir Facility Services Kostelac
Birkenhaldweg 14
6338 Haldenau
www.varomir-fs.ch
Person data:
Tarik Kostelac
Geschäftsführer
+41 76 519 47 83
info@varomir-fs.ch
Back side:
could be colored in blue or green
please use a big logo sing and some smaller icons to say what is all beeing offered in facility services, like cleaning, maintenance cleaning
industrial cleaning, caretaking, gardening, disposal. There is no need for everyone of the icons if there are similar or an icon is standing for more of them.
colors to use:
blue: HEX 246BB0
green: HEX 52B33E

```html
<!DOCTYPE html>
<html lang="de">
<head>
<meta charset="utf-8">
<title>Varomir Facility Services – Business Card</title>
<link href="https://fonts.googleapis.com/css2?family=Roboto:wght@400;500;700&display=swap" rel="stylesheet">
<style>
  :root {
    --blue: #246BB0;
    --blue-dark: #1757a8;
    --green: #52B33E;
    --green-text: #1fa33a;
    --ink: #1d1d1d;
    --paper: #ffffff;
    --stage: #d9d9db;
  }
  * { box-sizing: border-box; margin: 0; padding: 0; }
  html, body { width: 1200px; height: 1200px; overflow: hidden; }
  body {
    background: var(--stage);
    font-family: "Roboto", Arial, sans-serif;
    display: flex; flex-direction: column; align-items: center; justify-content: center;
    gap: 44px;
  }
  .card {
    position: relative;
    width: 900px; height: 520px;
    border-radius: 34px;
    overflow: hidden;
    box-shadow: 0 10px 28px rgba(0,0,0,.25);
  }

  /* Back side */
  .card--back { background: var(--blue); color: var(--paper); }
  .brand-block {
    position: absolute; top: 70px; left: 0; right: 0;
    display: flex; flex-direction: column; align-items: center; gap: 14px;
  }
  .brand-mark {
    width: 34px; height: 34px; border-radius: 50%; background: var(--paper); flex: none;
  }
  .brand-name {
    font-weight: 700; font-size: 58px; letter-spacing: 3px; text-transform: uppercase;
    text-align: center; line-height: 1.05;
  }
  .services {
    position: absolute; left: 0; right: 0; bottom: 60px;
    display: flex; justify-content: center; gap: 54px;
  }
  .service { display: flex; flex-direction: column; align-items: center; gap: 12px; width: 140px; }
  .service__icon {
    width: 96px; height: 96px; border-radius: 50%;
    border: 3px solid var(--paper);
    display: flex; align-items: center; justify-content: center;
  }
  .service__icon-fill {
    width: 78px; height: 78px; border-radius: 50%;
    border: 2px solid var(--paper);
    background: rgba(255,255,255,.18);
  }
  .service__label {
    font-weight: 700; font-size: 15px; text-transform: uppercase; text-align: center; line-height: 1.1;
  }

  /* Front side */
  .card--front { background: var(--paper); color: var(--ink); }
  .tab { position: absolute; left: 0; top: 62px; width: 38px; height: 52px; background: var(--blue-dark); }
  .person { position: absolute; left: 64px; top: 58px; }
  .person__name { color: var(--blue-dark); font-weight: 700; font-size: 34px; }
  .person__role { font-size: 17px; margin-top: 4px; }
  .company { position: absolute; left: 64px; top: 258px; font-size: 21px; line-height: 1.22; }
  .company__name { color: var(--green-text); font-weight: 700; }
  .contact { list-style: none; margin-top: 16px; }
  .contact li { display: flex; align-items: center; gap: 10px; }
  .contact svg { width: 18px; height: 18px; flex: none; }
  .contact .web-accent { color: var(--blue-dark); font-weight: 500; }
  .front-brand {
    position: absolute; right: 56px; bottom: 54px;
    display: flex; align-items: center; gap: 14px;
  }
  .front-brand .brand-mark { background: var(--blue); width: 26px; height: 26px; }
  .front-brand .brand-name { color: var(--blue); font-size: 34px; letter-spacing: 2px; text-align: left; }
</style>
</head>
<body>

<section class="card card--back" aria-label="Back side">
  <div class="brand-block">
    <span class="brand-mark"></span>
    <div class="brand-name">Varomir<br>Facility Services</div>
  </div>
  <div class="services">
    <div class="service">
      <div class="service__icon"><div class="service__icon-fill" role="img" aria-label="Cleaning brush icon"></div></div>
      <div class="service__label">Maintenance<br>Cleaning</div>
    </div>
    <div class="service">
      <div class="service__icon"><div class="service__icon-fill" role="img" aria-label="Handshake icon"></div></div>
      <div class="service__label">Caretaking</div>
    </div>
    <div class="service">
      <div class="service__icon"><div class="service__icon-fill" role="img" aria-label="Flower pot icon"></div></div>
      <div class="service__label">Gardening</div>
    </div>
    <div class="service">
      <div class="service__icon"><div class="service__icon-fill" role="img" aria-label="Waste bin icon"></div></div>
      <div class="service__label">Disposal</div>
    </div>
  </div>
</section>

<section class="card card--front" aria-label="Front side">
  <div class="tab"></div>
  <div class="person">
    <div class="person__name">Tarik Kostelac</div>
    <div class="person__role">Geschäftsführer</div>
  </div>
  <div class="company">
    <div class="company__name">Varomir Facility Services Kostelac</div>
    <div>Birkenhaldweg 14</div>
    <div>6338 Haldenau</div>
    <ul class="contact">
      <li>
        <svg viewBox="0 0 24 24" fill="var(--blue-dark)"><path d="M6.6 10.8a15 15 0 0 0 6.6 6.6l2.2-2.2c.3-.3.7-.4 1-.2 1.1.4 2.3.6 3.6.6.6 0 1 .4 1 1V20c0 .6-.4 1-1 1A17 17 0 0 1 3 4c0-.6.4-1 1-1h3.5c.6 0 1 .4 1 1 0 1.3.2 2.5.6 3.6.1.3 0 .7-.2 1z"/></svg>
        <span>+41 76 519 47 83</span>
      </li>
      <li>
        <svg viewBox="0 0 24 24" fill="none" stroke="var(--blue-dark)" stroke-width="2"><rect x="3" y="5" width="18" height="14" rx="1"/><path d="M3 6l9 7 9-7"/></svg>
        <span>info@varomir-fs.ch</span>
      </li>
      <li>
        <svg viewBox="0 0 24 24" fill="none" stroke="var(--blue-dark)" stroke-width="1.8"><circle cx="12" cy="12" r="9"/><path d="M3 12h18M12 3c3 3 3 15 0 18M12 3c-3 3-3 15 0 18"/></svg>
        <span>www.<span class="web-accent">varomir-fs</span>.ch</span>
      </li>
    </ul>
  </div>
  <div class="front-brand">
    <span class="brand-mark"></span>
    <div class="brand-name">Varomir<br>Facility Services</div>
  </div>
</section>

</body>
</html>
```